Business card por a urban DJ, up scale audience target

Need a sober design, modern, conservative colors but i can consider some options, y play rnb, hip hop, EDM and top40.

Business card for contact and personal info, double sided, use logo attrached please; im 42 so i need a card acording to my age an target audience.

Target Market(s)

Adult people, up scale audience

Industry/Entity Type

Music Download

Contact Information for Business Card

Cel (318) 4207265518 www.lumadrift.com

Requirements
Must have
• open mind
Nice to have
• open mind
Should not have
• DJ

```html
<!DOCTYPE html>
<html lang="en">
<head>
<meta charset="utf-8">
<title>Lumadrift – Business Card</title>
<link href="https://fonts.googleapis.com/css2?family=Noto+Sans:wght@400;700&display=swap" rel="stylesheet">
<style>
  :root {
    --backdrop: #2b2b2d;
    --card: #1f2022;
    --ink: #ffffff;
    --ink-soft: #e6e6e6;
    --rule: #cfcfcf;
  }
  * { box-sizing: border-box; margin: 0; padding: 0; }
  html, body {
    width: 1200px; height: 1189px; overflow: hidden;
    background: var(--backdrop);
    font-family: "Noto Sans", Verdana, sans-serif;
    color: var(--ink);
  }
  .sheet {
    width: 1200px; height: 1189px;
    display: flex; flex-direction: column; align-items: center; justify-content: center;
    gap: 64px;
  }
  .card {
    width: 880px; height: 503px;
    background: var(--card);
    border-radius: 34px;
    position: relative;
    box-shadow: 0 14px 30px rgba(0,0,0,.45);
  }
  .wordmark {
    display: flex; align-items: center; gap: 18px;
    font-weight: 700; letter-spacing: 2px; color: var(--ink);
  }
  .wordmark__mark { background: var(--ink); }

  .card--front { display: flex; align-items: center; justify-content: center; }
  .card--front .wordmark { font-size: 84px; }
  .card--front .wordmark__mark { width: 40px; height: 40px; }

  .card--back { display: flex; align-items: center; }
  .card--back .brand-side {
    width: 470px; height: 100%;
    display: flex; align-items: center; justify-content: center;
  }
  .card--back .wordmark { font-size: 56px; }
  .card--back .wordmark__mark { width: 28px; height: 28px; }
  .divider {
    width: 2px; height: 330px;
    background: linear-gradient(to bottom, transparent, var(--rule) 15%, var(--rule) 85%, transparent);
  }
  .details { padding-left: 52px; }
  .details__name { font-size: 27px; font-weight: 700; letter-spacing: 1px; line-height: 1.1; }
  .details__role { font-size: 17px; color: var(--ink-soft); margin-bottom: 34px; }
  .details__address { font-size: 19px; line-height: 1.3; color: var(--ink-soft); }
  .contacts { list-style: none; margin-top: 8px; }
  .contacts li {
    display: flex; align-items: center; gap: 10px;
    font-size: 21px; line-height: 1.45;
  }
  .contacts svg { width: 24px; height: 24px; flex: none; }
</style>
</head>
<body>
<main class="sheet">
  <section class="card card--front">
    <div class="wordmark"><span class="wordmark__mark"></span>LUMADRIFT</div>
  </section>

  <section class="card card--back">
    <div class="brand-side">
      <div class="wordmark"><span class="wordmark__mark"></span>LUMADRIFT</div>
    </div>
    <div class="divider"></div>
    <div class="details">
      <p class="details__name">EMPLOYEE NAME</p>
      <p class="details__role">Development Manager</p>
      <p class="details__address">P.O. Box 214, Harbour Row<br>Wrenfield, Northvale<br>(318) 4207265518</p>
      <ul class="contacts">
        <li>
          <svg viewBox="0 0 24 24" aria-hidden="true"><rect width="24" height="24" rx="4" fill="#fff"/><rect x="8" y="4" width="8" height="16" rx="1.5" fill="none" stroke="#1f2022" stroke-width="1.8"/><rect x="10" y="6.5" width="4" height="6" fill="#1f2022"/></svg>
          (318) 4207265518
        </li>
        <li>
          <svg viewBox="0 0 24 24" aria-hidden="true"><rect width="24" height="24" rx="4" fill="#fff"/><rect x="4.5" y="7" width="15" height="10" fill="none" stroke="#1f2022" stroke-width="1.6"/><path d="M4.5 7 12 13l7.5-6" fill="none" stroke="#1f2022" stroke-width="1.6"/></svg>
          hello@lumadrift.com
        </li>
        <li>
          <svg viewBox="0 0 24 24" aria-hidden="true"><rect width="24" height="24" rx="4" fill="#fff"/><circle cx="12" cy="12" r="7" fill="none" stroke="#1f2022" stroke-width="1.6"/><ellipse cx="12" cy="12" rx="3" ry="7" fill="none" stroke="#1f2022" stroke-width="1.4"/><path d="M5 12h14" stroke="#1f2022" stroke-width="1.4"/></svg>
          www.lumadrift.com
        </li>
      </ul>
    </div>
  </section>
</main>
</body>
</html>
```